Dog grooming business card
This is a business card for m dog grooming business like it say above.
In the priorities box below I will have the text that I want on the card.

Industry/Entity Type

Business

Colors

Designer to choose colors to be used in the design.

Requirements
Must have
• My logo and the insurance stamp must be on the card.

Text it must have :

Professional grooming services
Email: lunabrisk@mailvale.net
Text or call 1 705 318 6052
TWF certified/member
Pet first aid certified
Next appointment ___________________________________
Nice to have
• Greens to match my logo

```html
<!DOCTYPE html>
<html lang="en">
<head>
<meta charset="utf-8">
<title>Luna Brisk – Grooming Business Card</title>
<link rel="stylesheet" href="https://fonts.googleapis.com/css2?family=Marcellus+SC&family=Montserrat:wght@400;600;700&display=swap">
<style>
  :root {
    --bg-light: #ececec;
    --bg-dark: #b9b9b9;
    --card-white: #ffffff;
    --red: #d3182c;
    --red-deep: #9c1420;
    --red-text: #b0141f;
    --wine: #8a1a1a;
    --shadow: rgba(0,0,0,0.28);
  }
  * { box-sizing: border-box; margin: 0; padding: 0; }
  html, body { width: 1200px; height: 1000px; overflow: hidden; }
  body {
    background: radial-gradient(ellipse at 50% 20%, var(--bg-light) 0%, #d4d4d4 55%, var(--bg-dark) 100%);
    position: relative;
    font-family: "Marcellus SC", serif;
  }
  .card {
    position: absolute;
    top: 335px;
    width: 540px;
    height: 330px;
    background: var(--card-white);
    box-shadow: 0 14px 30px var(--shadow);
    overflow: hidden;
  }
  .card--back { left: 40px; }
  .card--front { left: 620px; }
  .card__waves { position: absolute; inset: 0; width: 100%; height: 100%; }

  /* back card */
  .insurer { position: absolute; left: 46px; top: 30px; }
  .insurer__label {
    font-family: "Montserrat", sans-serif;
    font-size: 8px; letter-spacing: 2px; color: #9a9a9a; margin-left: 4px;
  }
  .insurer__name {
    font-family: "Montserrat", sans-serif;
    font-weight: 700; font-size: 34px; color: var(--red-text); line-height: 1;
  }
  .insurer__tagline {
    font-family: "Montserrat", sans-serif;
    font-size: 8px; letter-spacing: 1px; color: var(--red-text); margin-top: 3px; margin-left: 2px;
  }
  .splash-area {
    position: absolute; left: 56px; top: 128px; width: 170px; height: 120px;
    border-radius: 12px;
    background: linear-gradient(160deg, #e3203c 0%, #c3142a 100%);
  }
  .contact-list {
    position: absolute; left: 268px; top: 92px; list-style: none;
    color: var(--red-text); font-size: 13px; line-height: 1;
  }
  .contact-list li { display: flex; align-items: center; gap: 8px; height: 22px; white-space: nowrap; }
  .contact-list .icon { width: 14px; height: 12px; flex: none; fill: var(--red-text); }
  .contact-list .lead { font-size: 14px; }
  .contact-list .appointment { margin-top: 4px; }
  .appointment__blank {
    display: inline-block; width: 92px; border-bottom: 1px solid var(--red-text);
    height: 11px;
  }

  /* front card */
  .brand {
    position: absolute; left: 22px; top: 112px; display: flex; align-items: center; gap: 10px;
  }
  .brand__mark { width: 22px; height: 22px; border-radius: 50%; background: var(--red-deep); }
  .brand__name { font-size: 24px; color: var(--red-deep); }
  .stamp {
    position: absolute; right: 22px; top: 40px; width: 96px; height: 58px;
    border: 1.5px solid var(--red); border-radius: 8px; background: #fff;
    display: flex; flex-direction: column; align-items: center; justify-content: center;
  }
  .stamp__label { font-family: "Montserrat", sans-serif; font-size: 6px; letter-spacing: 1px; color: #999; }
  .stamp__name { font-family: "Montserrat", sans-serif; font-weight: 700; font-size: 15px; color: var(--red-text); }
  .headline {
    position: absolute; left: 200px; top: 118px; width: 260px; text-align: center;
    color: var(--wine); font-size: 17px; font-weight: 400; line-height: 1.45; letter-spacing: 0.5px;
  }
  .mascot {
    position: absolute; right: 34px; top: 190px; width: 100px; height: 120px; border-radius: 40% 40% 30% 30%;
    background: linear-gradient(180deg, #e7a6cf 0%, #c98ac0 45%, #8fb2e2 100%);
  }
</style>
</head>
<body>

<section class="card card--back" aria-label="Business card, contact side">
  <svg class="card__waves" viewBox="0 0 540 330" preserveAspectRatio="none" aria-hidden="true">
    <defs>
      <linearGradient id="backRed" x1="0" y1="0" x2="1" y2="1">
        <stop offset="0" stop-color="#e11b33"/>
        <stop offset="0.6" stop-color="#c8142a"/>
        <stop offset="1" stop-color="#9c1420"/>
      </linearGradient>
    </defs>
    <path d="M0 235 C120 190 220 218 300 262 C380 305 460 312 540 298 L540 330 L0 330 Z" fill="url(#backRed)"/>
    <path d="M0 227 C120 182 220 210 300 254 C380 297 460 304 540 290" fill="none" stroke="#c8142a" stroke-width="1.2"/>
  </svg>

  <div class="insurer">
    <div class="insurer__label">PROTECTED BY</div>
    <div class="insurer__name">CareGuard</div>
    <div class="insurer__tagline">INSURANCE FOR PET CARE</div>
  </div>

  <div class="splash-area" role="img" aria-label="Red paint splatter illustration with paw prints"></div>

  <ul class="contact-list">
    <li class="lead">
      <svg class="icon" viewBox="0 0 14 12" aria-hidden="true"><rect x="2" y="2" width="10" height="8"/></svg>
      Professional grooming services
    </li>
    <li>
      <svg class="icon" viewBox="0 0 14 12" aria-hidden="true"><rect x="0" y="1" width="14" height="10"/><path d="M0 1 L7 7 L14 1" fill="none" stroke="#fff" stroke-width="1.2"/></svg>
      lunabrisk@mailvale.net
    </li>
    <li>
      <svg class="icon" viewBox="0 0 14 12" aria-hidden="true"><path d="M1 4 Q7 -1 13 4 L11 6 L9 4 L5 4 L3 6 Z"/><rect x="3" y="6" width="8" height="5" rx="1"/></svg>
      1 705 318 6052
    </li>
    <li>
      <svg class="icon" viewBox="0 0 14 12" aria-hidden="true"><path d="M0 3 H8 V0 L14 6 L8 12 V9 H0 Z"/></svg>
      TWF certified/member
    </li>
    <li>
      <svg class="icon" viewBox="0 0 14 12" aria-hidden="true"><path d="M0 3 H8 V0 L14 6 L8 12 V9 H0 Z"/></svg>
      Pet first aid certified
    </li>
    <li class="appointment">
      <svg class="icon" viewBox="0 0 14 12" aria-hidden="true"><path d="M0 3 H8 V0 L14 6 L8 12 V9 H0 Z"/></svg>
      Next appointment <span class="appointment__blank" aria-hidden="true"></span>
    </li>
  </ul>
</section>

<section class="card card--front" aria-label="Business card, brand side">
  <svg class="card__waves" viewBox="0 0 540 330" preserveAspectRatio="none" aria-hidden="true">
    <defs>
      <linearGradient id="frontRed" x1="0" y1="0" x2="1" y2="1">
        <stop offset="0" stop-color="#e11b33"/>
        <stop offset="1" stop-color="#a8141f"/>
      </linearGradient>
    </defs>
    <rect x="0" y="0" width="540" height="26" fill="#b5161f"/>
    <line x1="0" y1="32" x2="540" y2="32" stroke="#b5161f" stroke-width="1"/>
    <path d="M0 225 C110 175 220 180 310 210 C400 240 470 235 540 215 L540 330 L0 330 Z" fill="url(#frontRed)"/>
    <path d="M0 218 C110 168 220 173 310 203 C400 233 470 228 540 208" fill="none" stroke="#c8142a" stroke-width="1.2"/>
  </svg>

  <div class="brand">
    <span class="brand__mark" aria-hidden="true"></span>
    <span class="brand__name">Luna Brisk</span>
  </div>

  <div class="stamp">
    <span class="stamp__label">PROTECTED BY</span>
    <span class="stamp__name">CareGuard</span>
  </div>

  <h1 class="headline">Professional Grooming Services</h1>

  <div class="mascot" role="img" aria-label="Illustration of a small groomed dog in a blue coat"></div>
</section>

</body>
</html>
```